we are an outdoor outlet in a country club that has a variety of outlets. The Club is called Meadowlark and is located in Cairo, Egypt. This garden menu will include cuisines from the Mediterranean, Asia and Texmex. we need a menu that is colorful and would fit an A3 size, back and front are to be used. Attached is the old menu currently in use (Garden Menu 2012.pdf is just for reference) and the new menu text for you to use is under the name Garden Menu Fall 2013
thank you.
Updates
Logo files have been uploaded for this project
Industry/Entity Type
Club
Look and feel
Each slider illustrates characteristics of the customer's brand and the style your logo design should communicate.

```html
<!DOCTYPE html>
<html lang="en">
<head>
<meta charset="utf-8">
<title>Meadowlark Garden Menu Cover</title>
<link rel="stylesheet" href="https://fonts.googleapis.com/css2?family=Great+Vibes&family=Open+Sans:wght@400&display=swap">
<style>
  :root {
    --leaf: #8fa83e;
    --leaf-deep: #8aa43a;
    --paper: #ffffff;
    --bark: #4a2a1c;
  }
  html, body {
    margin: 0;
    padding: 0;
    width: 1200px;
    height: 865px;
    overflow: hidden;
    background: var(--paper);
  }
  .spread {
    position: relative;
    width: 1200px;
    height: 865px;
  }
  .spread svg {
    position: absolute;
    inset: 0;
  }
  .menu-title {
    position: absolute;
    left: 800px;
    top: 250px;
    width: 160px;
    margin: 0;
    font-family: "Great Vibes", cursive;
    font-weight: 400;
    font-size: 44px;
    line-height: 40px;
    color: var(--paper);
    text-align: center;
  }
  .menu-title span { display: block; }
  .menu-title .second { padding-left: 22px; }
  .club-name {
    position: absolute;
    left: 770px;
    top: 700px;
    width: 230px;
    display: flex;
    align-items: center;
    justify-content: center;
    gap: 12px;
  }
  .club-name .dot {
    flex: none;
    width: 30px;
    height: 30px;
    border-radius: 50%;
    background: var(--leaf);
  }
  .club-name .word {
    font-family: "Open Sans", sans-serif;
    font-weight: 400;
    font-size: 34px;
    line-height: 1;
    letter-spacing: 0.5px;
    color: var(--bark);
  }
</style>
</head>
<body>
<main class="spread">
  <svg width="1200" height="865" viewBox="0 0 1200 865" xmlns="http://www.w3.org/2000/svg">
    <defs>
      <filter id="panel-shadow" x="-5%" y="-5%" width="110%" height="112%">
        <feDropShadow dx="3" dy="6" stdDeviation="4" flood-color="#000" flood-opacity="0.28"/>
      </filter>
      <linearGradient id="cover-fade" gradientUnits="userSpaceOnUse" x1="0" y1="100" x2="0" y2="838">
        <stop offset="0" stop-color="#8aa43a"/>
        <stop offset="0.17" stop-color="#8fa83e"/>
        <stop offset="0.45" stop-color="#c9d6a0"/>
        <stop offset="0.8" stop-color="#ffffff"/>
        <stop offset="1" stop-color="#ffffff"/>
      </linearGradient>
    </defs>

    <rect class="back-panel" x="24" y="28" width="573" height="810" fill="var(--leaf)" filter="url(#panel-shadow)"/>

    <path class="cover-panel" filter="url(#panel-shadow)" fill="url(#cover-fade)"
      d="M597,838 L597,192 C600,172 616,166 650,165 C690,164 720,180 745,193 L764,193 L764,150
         C764,112 782,100 830,100 C860,100 874,108 882,118 C890,108 905,100 935,100
         C985,100 1002,115 1002,150 L1002,193 L1022,193 C1050,180 1080,165 1120,165
         C1150,165 1168,176 1168,200 L1168,838 Z"/>

    <rect class="chef-hat" role="img" aria-label="Outline drawing of a chef's hat"
      x="824" y="186" width="80" height="60" rx="20" fill="#ffffff" fill-opacity="0.22"/>
  </svg>

  <h1 class="menu-title"><span>Menu</span><span class="second">Card</span></h1>

  <div class="club-name">
    <span class="dot"></span>
    <span class="word">Meadowlark</span>
  </div>
</main>
</body>
</html>
```